Redesign and move to Wordpress for corvandel.com

Our website needs a redesign and at the same time we are moving it to Wordpress. Please help us with a new digital professional look and feel.

We are an Australian Software Engineering company specialising in advanced software development using in A.I., PLatform Engineering, Integration and Cloud. See the current corvandel.com for more information about us.

```html
<!DOCTYPE html>
<html lang="en">
<head>
<meta charset="utf-8">
<title>Corvandel — Reliable Smart Software Engineering</title>
<link href="https://fonts.googleapis.com/css2?family=Lexend+Exa:wght@500;600&family=Poppins:wght@400;500;600;700&display=swap" rel="stylesheet">
<style>
:root{
  --teal:#3bb3ad;
  --teal-dark:#2a9d97;
  --navy:#1f4e8c;
  --navy-deep:#163a6b;
  --ink:#2b2b2b;
  --muted:#555;
  --grey-band:#ebebeb;
  --slate:#2f4a6b;
  --footer:#0e1b31;
  --white:#fff;
}
*{margin:0;padding:0;box-sizing:border-box}
html,body{width:1200px;height:4766px;overflow:hidden}
body{position:relative;background:var(--white);font-family:"Poppins",sans-serif;color:var(--ink)}
.abs{position:absolute}
.display{font-family:"Lexend Exa",sans-serif;font-weight:600;letter-spacing:2px}
.btn{position:absolute;display:flex;align-items:center;justify-content:center;font-family:"Lexend Exa",sans-serif;font-weight:500;font-size:14px;letter-spacing:1px;color:var(--white)}

/* header */
.site-header{top:0;left:0;width:1200px;height:82px;background:var(--white);box-shadow:0 2px 6px rgba(0,0,0,.06);z-index:3}
.brand{left:74px;top:18px;display:flex;align-items:center;gap:14px}
.brand-mark{width:44px;height:44px;border:5px solid var(--teal)}
.brand-name{font-family:"Poppins",sans-serif;font-weight:400;font-size:40px;color:var(--navy);line-height:1}
.main-nav{top:30px;left:515px;display:flex;gap:52px;font-family:"Lexend Exa",sans-serif;font-size:15px;color:var(--ink)}
.main-nav .active{color:var(--teal)}
.search-icon{left:1108px;top:32px}

/* hero */
.hero{top:82px;left:0;width:1200px;height:690px;background:linear-gradient(110deg,#05121f 0%,#0c2a3c 40%,#1d5a70 70%,#0a2233 100%)}
.hero-title{left:74px;top:210px;font-size:68px;color:var(--white);letter-spacing:4px}
.hero-sub{left:74px;top:282px;font-family:"Poppins",sans-serif;font-weight:700;font-size:34px;line-height:40px;color:var(--white)}
.hero .btn{left:74px;top:380px;width:180px;height:48px;border-radius:24px;background:var(--teal)}
.dots{left:74px;top:580px;display:flex;gap:10px}
.dots span{width:14px;height:14px;border-radius:50%;border:2px solid var(--white)}
.dots span.on{background:var(--navy);border-color:var(--navy)}

.divider{position:absolute;left:0;width:1200px}

/* about */
.about-tile{position:absolute;border:5px solid var(--teal);background:linear-gradient(135deg,#1a48c8,#2a8fd6)}
.about-title{left:543px;top:892px;font-size:44px;color:var(--ink)}
.about-text{left:543px;top:952px;width:590px;font-size:17px;line-height:34px;color:var(--ink)}
.about .btn{left:543px;top:1149px;width:152px;height:46px;background:var(--navy)}

/* services */
.services-band{top:1360px;left:0;width:1200px;height:580px;background:var(--grey-band)}
.section-title{width:1200px;text-align:center;font-size:44px;color:var(--ink)}
.service-card{position:absolute;top:1565px;width:242px;height:258px;background:var(--white);border-radius:26px;text-align:center;padding:72px 22px 0}
.service-card.featured{background:var(--navy)}
.service-card h3{font-size:13px;font-weight:600;color:var(--navy);line-height:22px;text-transform:uppercase;margin-bottom:8px}
.service-card p{font-size:13px;line-height:22px;color:var(--ink)}
.service-card.featured h3,.service-card.featured p{color:var(--white)}
.service-icon{position:absolute;top:1524px;width:90px;height:90px;border-radius:50%;display:flex;align-items:center;justify-content:center}
.circle-arrow{position:absolute;border-radius:50%;display:flex;align-items:center;justify-content:center}

/* partners */
.partner{position:absolute;top:2040px;font-family:"Poppins",sans-serif;font-weight:700;font-size:38px;color:#1a1a1a;display:flex;align-items:center;gap:12px}
.partner i{display:block;width:26px;height:26px;background:#1a1a1a}

/* booking */
.book-sub{top:2355px;width:1200px;text-align:center;font-size:16px;color:var(--navy)}
.booking{left:246px;top:2413px;width:710px;height:550px;background:var(--white);box-shadow:0 2px 12px rgba(0,0,0,.15)}
.booking-side{left:0;top:0;width:355px;height:550px;background:var(--slate);color:var(--white)}
.avatar{left:145px;top:42px;width:64px;height:64px;border-radius:50%;background:#8a8a8a;border:3px solid #fff}
.meet{left:0;top:125px;width:355px;text-align:center;font-size:19px}
.month{left:0;top:160px;width:355px;text-align:center;font-size:19px;font-weight:500}
.cal{left:12px;top:208px;width:331px;display:grid;grid-template-columns:repeat(7,1fr);row-gap:24px;text-align:center;font-size:11px}
.cal .h{font-weight:600;font-size:12px}
.cal .d{opacity:.35;height:20px;line-height:20px}
.cal .a{opacity:1;font-weight:600}
.cal .sel{opacity:1;justify-self:center;width:40px;height:40px;margin-top:-10px;line-height:40px;border-radius:50%;background:#fff;color:var(--slate);font-weight:600}
.label{font-size:13px;font-weight:600;color:var(--slate)}
.slot{position:absolute;left:386px;width:273px;height:40px;border:1px solid #ccd;border-radius:2px;display:flex;align-items:center;justify-content:center;font-size:14px;color:var(--navy)}

/* news */
.news-title{left:74px;top:3150px;font-size:44px;color:var(--ink)}
.news-sub{left:74px;top:3216px;font-size:17px;color:var(--navy)}
.news-card{position:absolute;top:3261px;width:330px}
.news-img{width:330px;height:192px}
.news-card h3{margin-top:30px;font-size:20px;font-weight:700;line-height:29px;color:var(--ink)}
.news-card .cat{margin-top:10px;font-size:12px;font-weight:500;color:var(--navy);text-transform:uppercase}
.news-card p{margin-top:10px;font-size:13px;line-height:22px;color:var(--muted)}
.news-btn{left:519px;top:3711px;width:201px;height:46px;background:var(--teal)}

/* newsletter */
.newsletter{top:3800px;left:0;width:1200px;height:520px;background:linear-gradient(180deg,#0f2f5c 0%,#163f74 55%,#0d2447 100%)}
.news-head{width:1200px;text-align:center;font-size:42px;line-height:52px;color:var(--white);letter-spacing:3px}
.news-head .accent{color:var(--teal)}
.reg{top:4094px;width:1200px;text-align:center;font-size:19px;color:var(--white)}
.subscribe{left:209px;top:4150px;width:782px;height:56px;background:var(--white);display:flex;border:2px solid var(--teal)}
.subscribe span{flex:1;padding-left:16px;line-height:52px;font-size:12px;color:#444}
.subscribe b{width:136px;background:var(--teal);color:#fff;font-size:12px;font-weight:600;letter-spacing:1px;display:flex;align-items:center;justify-content:center}

/* footer */
.site-footer{top:4320px;left:0;width:1200px;height:446px;background:var(--footer);color:#d7dbe3}
.foot-brand{left:74px;top:120px;display:flex;align-items:center;gap:14px}
.foot-brand .brand-mark{border-color:var(--teal)}
.foot-brand .brand-name{color:var(--white)}
.contact{left:74px;font-size:13px;line-height:22px;display:flex;gap:14px}
.contact svg{flex:none;margin-top:4px}
.foot-col h4{font-family:"Lexend Exa",sans-serif;font-weight:500;font-size:19px;color:var(--teal);margin-bottom:14px}
.foot-col li{list-style:none;font-size:14px;line-height:34px}
.foot-rule{left:0;top:370px;width:1200px;height:1px;background:#25324a}
.copyright{left:74px;top:408px;font-size:13px}
.social{left:958px;top:400px;display:flex;gap:20px}
.social span{width:22px;height:22px;border-radius:50%;background:#fff}
.tag{left:1166px;top:410px;font-size:11px}
</style>
</head>
<body>

<header class="abs site-header">
  <div class="abs brand"><span class="brand-mark"></span><span class="brand-name">corvandel</span></div>
  <nav class="abs main-nav"><span class="active">HOME</span><span>ABOUT US</span><span>SERVICES</span><span>CONTACT US</span></nav>
  <svg class="abs search-icon" width="18" height="18" viewBox="0 0 18 18"><circle cx="7" cy="7" r="5" fill="none" stroke="#1f4e8c" stroke-width="2.5"/><line x1="11" y1="11" x2="16" y2="16" stroke="#1f4e8c" stroke-width="2.5"/></svg>
</header>

<section class="abs hero" role="img" aria-label="Software engineer with glasses looking at screens of code">
  <h1 class="abs display hero-title">CORVANDEL</h1>
  <p class="abs hero-sub">Reliable Smart<br>Software Engineering</p>
  <a class="btn">LEARN MORE</a>
  <div class="abs dots"><span class="on"></span><span></span><span></span><span></span></div>
</section>
<svg class="divider" style="top:700px" height="90" viewBox="0 0 1200 90" preserveAspectRatio="none"><polygon points="0,40 600,20 1200,30 1200,90 0,90" fill="#fff"/><polygon points="0,40 600,20 1200,30 1200,55 600,30 0,72" fill="#3bb3ad"/></svg>

<section class="about">
  <div class="about-tile" style="left:74px;top:837px;width:195px;height:132px" role="img" aria-label="Hands typing on a laptop in blue light"></div>
  <div class="about-tile" style="left:302px;top:837px;width:195px;height:260px" role="img" aria-label="Person using a tablet with digital overlays"></div>
  <div class="about-tile" style="left:74px;top:1000px;width:195px;height:263px;background:linear-gradient(135deg,#1b7fa8,#3ad0d8)" role="img" aria-label="Hand touching a digital interface"></div>
  <div class="about-tile" style="left:302px;top:1130px;width:195px;height:133px;background:linear-gradient(135deg,#1b8aa3,#4ac3d2)" role="img" aria-label="Team working at computers"></div>
  <h2 class="abs display about-title">ABOUT CORVANDEL</h2>
  <p class="abs about-text">At Corvandel, we craft bespoke software solutions that are not available on the market. By building organizations market-leading products, process automation, legacy system enablement, or advanced intelligent systems, we empower our customers to achieve a competitive edge in their industry.</p>
  <a class="btn">READ MORE</a>
</section>

<section>
  <div class="abs services-band"></div>
  <svg class="divider" style="top:1315px" height="70" viewBox="0 0 1200 70" preserveAspectRatio="none"><polygon points="0,0 1200,0 1200,45 600,60 0,45" fill="#fff"/><polygon points="0,10 600,58 1200,10 1200,40 600,66 0,40" fill="#3bb3ad"/></svg>
  <h2 class="abs display section-title" style="top:1428px">OUR SERVICES</h2>

  <div class="service-card" style="left:74px"><h3>Enterprise Systems<br>Integration</h3><p>Automate your business processes internally or externally to improve data quality and process efficiency.</p></div>
  <div class="service-card" style="left:344px"><h3>Micro Services</h3><p>Leverage Microservices Architecture to enable quick deployment, dynamically scalable service performance, team productivity and more.</p></div>
  <div class="service-card featured" style="left:614px"><h3>Platform<br>Engineering</h3><p>For organisations looking to manage the security and cost risks around their cloud infrastructure management for applications.</p></div>
  <div class="service-card" style="left:884px"><h3>Conversational AI</h3><p>Enabling legacy systems with conversational user interfaces, or simply building intelligent natural language based services.</p></div>

  <div class="service-icon" style="left:150px;background:var(--teal)"><svg width="40" height="40" viewBox="0 0 40 40" fill="none" stroke="#fff" stroke-width="2"><circle cx="20" cy="20" r="7"/><circle cx="20" cy="20" r="13" stroke-dasharray="4 4"/></svg></div>
  <div class="service-icon" style="left:420px;background:var(--navy)"><svg width="40" height="40" viewBox="0 0 40 40" fill="none" stroke="#fff" stroke-width="2"><circle cx="12" cy="12" r="5"/><circle cx="28" cy="12" r="5"/><circle cx="12" cy="28" r="5"/><circle cx="28" cy="28" r="5"/></svg></div>
  <div class="service-icon" style="left:690px;background:var(--teal)"><svg width="40" height="40" viewBox="0 0 40 40" fill="none" stroke="#fff" stroke-width="2"><rect x="6" y="9" width="28" height="20" rx="2"/><line x1="10" y1="15" x2="24" y2="15"/><line x1="10" y1="21" x2="20" y2="21"/></svg></div>
  <div class="service-icon" style="left:960px;background:var(--navy)"><svg width="40" height="40" viewBox="0 0 40 40" fill="none" stroke="#fff" stroke-width="2"><circle cx="15" cy="23" r="10"/><circle cx="26" cy="14" r="9"/></svg></div>

  <div class="circle-arrow" style="left:32px;top:1681px;width:26px;height:26px;background:#222"><svg width="10" height="12"><polygon points="9,0 0,6 9,12" fill="#fff"/></svg></div>
  <div class="circle-arrow" style="left:1141px;top:1681px;width:26px;height:26px;background:var(--teal)"><svg width="10" height="12"><polygon points="1,0 10,6 1,12" fill="#fff"/></svg></div>
  <svg class="divider" style="top:1920px" height="70" viewBox="0 0 1200 70" preserveAspectRatio="none"><polygon points="0,30 600,8 1200,20 1200,70 0,70" fill="#fff"/><polygon points="0,30 600,8 1200,20 1200,42 600,22 0,52" fill="#3bb3ad"/></svg>
</section>

<section>
  <div class="partner" style="left:84px">Harlow</div>
  <div class="partner" style="left:388px"><i></i>Quillon</div>
  <div class="partner" style="left:666px">Tarrant</div>
  <div class="partner" style="left:980px;font-weight:500;font-size:30px">Brightvale</div>
  <svg class="divider" style="top:2170px" height="60" viewBox="0 0 1200 60" preserveAspectRatio="none"><polygon points="0,5 600,35 1200,5 1200,25 600,48 0,25" fill="#3bb3ad"/></svg>
</section>

<section>
  <h2 class="abs display section-title" style="top:2290px">BOOK A FREE CONSULTATION</h2>
  <p class="abs book-sub">Book an obligation free consultation with our Lead Technologist</p>
  <div class="abs booking">
    <div class="abs booking-side">
      <div class="abs avatar" role="img" aria-label="Portrait of the CTO"></div>
      <div class="abs meet">Meet with our CTO</div>
      <div class="abs month">‹ &nbsp;January 2025&nbsp; ›</div>
      <div class="abs cal">
        <span class="h">SUN</span><span class="h">MON</span><span class="h">TUE</span><span class="h">WED</span><span class="h">THU</span><span class="h">FRI</span><span class="h">SAT</span>
        <span></span><span></span><span></span><span class="d">1</span><span class="d">2</span><span class="d">3</span><span class="d">4</span>
        <span class="d">5</span><span class="d">6</span><span class="d">7</span><span class="d">8</span><span class="d">9</span><span class="d">10</span><span class="d">11</span>
        <span class="d">12</span><span class="d">13</span><span class="d">14</span><span class="sel">15</span><span class="d a">16</span><span class="d a">17</span><span class="d">18</span>
        <span class="d">19</span><span class="d">20</span><span class="d">21</span><span class="d a">22</span><span class="d a">23</span><span class="d a">24</span><span class="d">25</span>
        <span class="d">26</span><span class="d">27</span><span class="d">28</span><span class="d a">29</span><span class="d a">30</span><span class="d a">31</span><span></span>
      </div>
    </div>
    <div class="abs label" style="left:386px;top:30px">Meeting duration</div>
    <div class="abs" style="left:386px;top:58px;width:283px;height:24px;background:#dde3ea;font-size:10px;text-align:center;line-height:24px;color:#667">30 mins</div>
    <div class="abs label" style="left:386px;top:110px">What time works best?</div>
    <div class="abs" style="left:386px;top:128px;font-size:12px;color:var(--slate)">Showing times for <b>January 15, 2025</b></div>
    <div class="abs" style="left:386px;top:168px;font-size:11px;font-weight:600;color:var(--navy)">UTC +05:30 New Delhi, Mumbai, Calcutta</div>
    <div class="slot" style="top:195px">3:30 am</div>
    <div class="slot" style="top:243px">3:45 am</div>
    <div class="slot" style="top:291px">4:00 am</div>
    <div class="slot" style="top:339px">4:15 am</div>
    <div class="slot" style="top:387px">4:30 am</div>
    <div class="slot" style="top:435px">4:45 am</div>
    <div class="slot" style="top:483px">5:00 am</div>
    <div class="abs" style="left:668px;top:198px;width:6px;height:320px;background:#eee"><div style="height:210px;background:#999"></div></div>
    <div class="abs" style="left:386px;top:523px;width:283px;height:27px;background:#fff"></div>
  </div>
  <svg class="divider" style="top:3035px" height="70" viewBox="0 0 1200 70" preserveAspectRatio="none"><polygon points="0,40 600,10 1200,40 1200,55 600,28 0,60" fill="#3bb3ad"/></svg>
</section>

<section>
  <h2 class="abs display news-title">NEWS &amp; ARTICLES</h2>
  <p class="abs news-sub">Updates from our industry</p>
  <div class="circle-arrow" style="left:1060px;top:3165px;width:26px;height:26px;background:#555"><svg width="10" height="12"><polygon points="9,0 0,6 9,12" fill="#fff"/></svg></div>
  <div class="circle-arrow" style="left:1100px;top:3165px;width:26px;height:26px;background:var(--teal)"><svg width="10" height="12"><polygon points="1,0 10,6 1,12" fill="#fff"/></svg></div>

  <article class="news-card" style="left:74px">
    <div class="news-img" role="img" aria-label="Two people at a whiteboard with a flow diagram" style="background:linear-gradient(135deg,#e8e8ea,#8d97a6)"></div>
    <h3>10 unexpected ways to use Helix Assist</h3>
    <div class="cat">AI in Software Engineering</div>
    <p>Helix Assist is widely known for its code generation feature. Learn how the AI assistant's abilities can extend beyond just code generation.</p>
  </article>
  <article class="news-card" style="left:435px">
    <div class="news-img" role="img" aria-label="Glowing data dashboard display in a dark room" style="background:linear-gradient(135deg,#0e1a24,#5d6a55)"></div>
    <h3>How Storytelling Helps Data-driven Teams Succeed</h3>
    <div class="cat">Business Insights</div>
    <p>Winning leaders know that data alone isn't enough. It's the art of storytelling that drives sustained performance.</p>
  </article>
  <article class="news-card" style="left:797px">
    <div class="news-img" role="img" aria-label="Colourful API diagram with connected icons" style="background:linear-gradient(135deg,#3a6fc4,#e4a8a0)"></div>
    <h3>PROMPTA: A general-purpose framework for prompt</h3>
    <div class="cat">Industry Research</div>
    <p>Large language models (LLMs) have revolutionized various tasks, but prompt engineering remains a challenge.</p>
  </article>
  <a class="btn news-btn">VIEW ALL NEWS</a>
</section>

<section>
  <div class="abs newsletter" role="img" aria-label="Night city skyline across a harbour"></div>
  <svg class="divider" style="top:3785px" height="50" viewBox="0 0 1200 50" preserveAspectRatio="none"><polygon points="0,0 1200,0 1200,10 600,30 0,10" fill="#fff"/><polygon points="0,10 600,30 1200,10 1200,22 600,42 0,22" fill="#3bb3ad"/></svg>
  <h2 class="abs display news-head" style="top:3920px">AUSTRALIA'S LARGEST HEALTH<br>CHARITY IMPLEMENTS<br><span class="accent">CORVANDEL API MSG BUS</span></h2>
  <p class="abs reg">Register to our newsletter to find out more.</p>
  <div class="abs subscribe"><span>Enter Email Address</span><b>SUBSCRIBE</b></div>
</section>

<footer class="abs site-footer">
  <div class="abs foot-brand"><span class="brand-mark"></span><span class="brand-name">corvandel</span></div>
  <div class="abs contact" style="top:196px"><svg width="12" height="12"><rect width="12" height="12" fill="#3bb3ad"/></svg><span>Suite 208, 42 Larkin Street<br>Southbank, VIC , 3006</span></div>
  <div class="abs contact" style="top:254px"><svg width="12" height="12" viewBox="0 0 12 12"><path d="M2 1 L5 1 L6 4 L4 5 Q5 7 7 8 L8 6 L11 7 L11 10 Q6 11 1 4 Z" fill="#3bb3ad"/></svg><span>1800 555 027</span></div>
  <div class="abs contact" style="top:286px"><svg width="12" height="12"><rect y="2" width="12" height="8" fill="#3bb3ad"/></svg><span>hello@corvandel.com</span></div>
  <div class="abs foot-col" style="left:410px;top:82px"><h4>SITE MAP</h4><ul><li>Home</li><li>About Us</li><li>Services</li><li>Contact Us</li></ul></div>
  <div class="abs foot-col" style="left:610px;top:82px"><h4>SERVICES</h4><ul><li>Enterprise Systems Integration</li><li>Microservices</li><li>Platform Engineering</li><li>Conversation A.I.</li><li>Integration Platform as a Service</li></ul></div>
  <div class="abs foot-col" style="left:884px;top:82px"><h4>&nbsp;</h4><ul><li>A.I. Agents</li><li>Real-time Data Stream Processing</li><li>Glidework</li><li>Technology Expertise</li></ul></div>
  <div class="abs foot-rule"></div>
  <div class="abs copyright">Copyright © 2025 Company Name All right reserved. Privacy Policy</div>
  <div class="abs social"><span></span><span></span><span></span><span></span><span></span></div>
  <div class="abs tag">x10</div>
</footer>

</body>
</html>
```